Redesign of Form/Document Navigation Page

I need a redesign of our document and navigation bar on the left. We want the same navigation bar layout/setup but want the buttons and typography to be simple and matching all over. The form needs to be aesthetically pleasing and fit within the page.

1st attachment is our Direct Deposit and the second is the form continued.

```html
<!DOCTYPE html>
<html lang="en">
<head>
<meta charset="utf-8">
<title>Sentinel Shield Services – Direct Deposit</title>
<link href="https://fonts.googleapis.com/css2?family=Open+Sans:wght@400;600;700&family=Montserrat:wght@400;500&display=swap" rel="stylesheet">
<style>
  :root {
    --navy: #1a1f7a;
    --gold: #f0b323;
    --page-bg: #e8e8e8;
    --panel: #ffffff;
    --border: #dddddd;
    --field: #f1f1f1;
    --field-border: #cfcfcf;
    --text: #222222;
    --muted: #555555;
    --soft: #666666;
  }
  * { box-sizing: border-box; margin: 0; padding: 0; }
  html, body { width: 1160px; height: 1200px; overflow: hidden; }
  body {
    position: relative;
    font-family: "Open Sans", Arial, sans-serif;
    color: var(--text);
    background: var(--panel);
  }
  .site-header {
    position: absolute; left: 0; top: 0; width: 1160px; height: 121px;
    background: var(--panel); border-bottom: 1px solid var(--border);
  }
  .brand {
    position: absolute; left: 106px; top: 38px;
    display: flex; align-items: center; gap: 10px;
  }
  .brand-mark { width: 46px; height: 46px; border-radius: 50%; background: var(--navy); }
  .brand-name {
    font-family: "Open Sans", Arial, sans-serif; font-weight: 700;
    font-size: 20px; line-height: 22px; color: var(--gold); letter-spacing: .3px;
  }
  .main-nav {
    position: absolute; left: 380px; top: 52px;
    display: flex; gap: 28px; font-size: 12px; color: var(--muted);
  }
  .main-nav .active { color: var(--navy); }
  .user {
    position: absolute; right: 107px; top: 48px;
    display: flex; align-items: center; gap: 14px;
    font-size: 14px; color: var(--soft);
  }
  .power { width: 24px; height: 24px; }

  .content {
    position: absolute; left: 0; top: 121px; width: 1160px; height: 987px;
    background: var(--page-bg);
  }
  .btn {
    display: inline-flex; align-items: center; justify-content: center;
    background: var(--navy); color: #fff; border-radius: 3px;
    font-family: "Open Sans", Arial, sans-serif;
  }
  .back-btn { position: absolute; left: 108px; top: 32px; width: 133px; height: 32px; font-size: 12px; }

  .side-nav {
    position: absolute; left: 108px; top: 95px; width: 219px; height: 575px;
    background: var(--panel); border: 1px solid var(--border);
    padding: 29px 0 0 17px;
  }
  .side-item {
    display: flex; align-items: center; gap: 12px; height: 47px; margin-bottom: 27.6px;
    font-size: 12px; color: var(--text);
  }
  .side-icon {
    width: 47px; height: 47px; border-radius: 50%; background: var(--navy);
    display: flex; align-items: center; justify-content: center; flex: none;
  }
  .side-icon svg { width: 24px; height: 24px; }

  .form-panel {
    position: absolute; left: 351px; top: 95px; width: 703px; height: 841px;
    background: var(--panel); border: 1px solid var(--border);
  }
  .form-title {
    position: absolute; left: 26px; top: 45px;
    font-family: "Montserrat", Arial, sans-serif; font-size: 14px; font-weight: 500; color: var(--text);
  }
  .terms { position: absolute; left: 26px; top: 80px; width: 650px; }
  .terms p { font-size: 10.8px; line-height: 24.9px; color: var(--muted); margin-bottom: 15px; }

  .label { position: absolute; font-size: 11px; color: var(--muted); }
  .field { position: absolute; background: var(--field); border: 1px solid var(--field-border); }
  .section-title {
    position: absolute; left: 29px; top: 314px;
    font-family: "Open Sans", Arial, sans-serif; font-size: 15px; font-weight: 600; color: #333;
  }
  .accept-btn { position: absolute; left: 29px; top: 631px; width: 125px; height: 27px; font-size: 11px; }
  .accept-btn { top: 510px; }

  .manager-title {
    position: absolute; left: 0; width: 100%; top: 592px; text-align: center;
    font-family: "Montserrat", Arial, sans-serif; font-size: 13.5px; color: var(--text);
  }
  .manager-box {
    position: absolute; left: 29px; top: 633px; width: 656px; height: 167px;
    border: 1px solid var(--field-border);
  }
  .manager-box .label { font-size: 12px; color: var(--muted); }

  .site-footer {
    position: absolute; left: 0; top: 1108px; width: 1160px; height: 92px;
    background: var(--panel); border-top: 1px solid var(--border);
    text-align: center; padding-top: 38px; font-size: 11px; color: var(--soft);
  }
</style>
</head>
<body>
  <header class="site-header">
    <div class="brand">
      <span class="brand-mark"></span>
      <span class="brand-name">SENTINEL SHIELD<br>SERVICES</span>
    </div>
    <nav class="main-nav">
      <span class="active">HOME</span><span>|</span><span>HELP</span>
    </nav>
    <div class="user">
      <span>Dana Whitfield</span>
      <svg class="power" viewBox="0 0 24 24" aria-label="Log out">
        <circle cx="12" cy="12" r="12" fill="#1a1f7a"/>
        <path d="M8.6 8.2a5 5 0 1 0 6.8 0" fill="none" stroke="#fff" stroke-width="1.8" stroke-linecap="round"/>
        <line x1="12" y1="6" x2="12" y2="11.5" stroke="#fff" stroke-width="1.8" stroke-linecap="round"/>
      </svg>
    </div>
  </header>

  <main class="content">
    <span class="btn back-btn">Back To Profile</span>

    <aside class="side-nav">
      <div class="side-item"><span class="side-icon"><svg viewBox="0 0 24 24" fill="none" stroke="#fff" stroke-width="1.4"><path d="M3 13l10-5 8 4-10 5z"/><path d="M3 15.5l8 4 10-5"/><path d="M3 10.5l10-5 8 4"/></svg></span>Direct Deposit</div>
      <div class="side-item"><span class="side-icon"><svg viewBox="0 0 24 24" fill="none" stroke="#fff" stroke-width="1.5"><rect x="4" y="5" width="13" height="15"/><path d="M7 9h7M7 12h7M7 15h4"/><path d="M20 3l-6 9"/></svg></span>Change W-4</div>
      <div class="side-item"><span class="side-icon"><svg viewBox="0 0 24 24" fill="none" stroke="#fff" stroke-width="1.5"><circle cx="12" cy="12" r="8"/><circle cx="12" cy="12" r="4"/><circle cx="12" cy="12" r="1" fill="#fff"/></svg></span>Labour Code</div>
      <div class="side-item"><span class="side-icon"><svg viewBox="0 0 24 24" fill="#fff"><circle cx="12" cy="8" r="4"/><path d="M4 20c0-4 3.5-6 8-6s8 2 8 6z"/></svg></span>Personal Information</div>
      <div class="side-item"><span class="side-icon"><svg viewBox="0 0 24 24" fill="#fff"><path d="M12 2.5l2.9 6.2 6.6.7-5 4.5 1.4 6.6L12 17.2l-5.9 3.3 1.4-6.6-5-4.5 6.6-.7z"/></svg></span>Appraisal and Review</div>
      <div class="side-item"><span class="side-icon"><svg viewBox="0 0 24 24" fill="none" stroke="#fff" stroke-width="1.5"><path d="M5 19l1-4L16 5l3 3L9 18z"/><path d="M14 7l3 3"/></svg></span>Write Up-Slip</div>
      <div class="side-item"><span class="side-icon"><svg viewBox="0 0 24 24" fill="#fff"><rect x="4" y="16" width="2.5" height="5"/><rect x="8" y="14" width="2.5" height="7"/><rect x="12" y="12" width="2.5" height="9"/><rect x="16" y="9" width="2.5" height="12"/><path d="M4 13l7-4 3 2 5-6" fill="none" stroke="#fff" stroke-width="1.5"/><path d="M16 4h4v4z"/></svg></span>Employee Performance</div>
    </aside>

    <section class="form-panel">
      <h1 class="form-title">IMPORTANT! Please read and sign before completing and submitting.</h1>
      <div class="terms">
        <p>I hereby authorize SENTINEL SHIELD SERVICES to deposit any amounts owed me, as instructed by my employer, by initiating credit entries to my account at the financial institution (hereinafter "Bank") indicated on this form. Further, I authorize Bank to accept and to credit any credit entries indicated by SENTINEL SHIELD SERVICES to my account. In the even that SENTINEL SHIELD SERVICES deposits funds erroneously into my account, I authorize SENTINEL SHIELD SERVICES to debit my account for an amount not to exceed the original amount of the erroneous credit.</p>
        <p>This authorization is to remain in full force and effect until SENTINEL SHIELD SERVICES and Bank have received written notice from me of its termination in such time and in such manner as to afford SENTINEL SHIELD SERVICES and Bank reasonable opportunity to act on it.</p>
      </div>

      <h2 class="section-title">Employee Name:</h2>
      <span class="label" style="left:29px; top:341px;">Employee Signature</span>
      <span class="field" style="left:29px; top:367px; width:203px; height:22px;"></span>
      <span class="field" style="left:29px; top:401px; width:203px; height:75px;"></span>
      <span class="label" style="left:341px; top:383px;">Sign Date</span>
      <span class="field" style="left:397px; top:379px; width:203px; height:22px;"></span>
      <span class="btn accept-btn">Accept Document</span>

      <h2 class="manager-title">ONLY PAYROLL MANAGER SIGNS BELOW</h2>
      <div class="manager-box">
        <span class="label" style="left:23px; top:13px;">Company Name:</span>
        <span class="field" style="left:22px; top:40px; width:306px; height:22px;"></span>
        <span class="label" style="left:23px; top:87px;">Employee File Number:</span>
        <span class="field" style="left:22px; top:115px; width:211px; height:22px;"></span>
        <span class="label" style="left:363px; top:13px;">Comments:</span>
        <span class="field" style="left:362px; top:40px; width:272px; height:70px;"></span>
      </div>
    </section>
  </main>

  <footer class="site-footer">Copyright © 2016 Sentinel Shield Services. All Right Reserved.</footer>
</body>
</html>
```